KVR Inc Web Design

WHAT ARE WE DOING?
We are developing a new website look and feel for a new company called KVR Inc. This new look and feel should include colors, design elements, choice of photography and other imagery, fonts, and other user experience elements.

WHAT DO THEY DO?
KVR, Inc, makes tools for researchers who are studying protein-protein interactions. These molecules are the basic tools of biology, and serve as key targets for drug developers and disease researchers. The world of proteins is enormously complex, and companies like KVR provide researchers with critical tools that help them elucidate this world.

WHO ARE WE TALKING TO?
The target audience for this website are professional scientists working in university research or biopharma drug development. They are highly sophisticated consumers looking for key tools that will advance their research.

WHAT DO WE WANT THEM TO DO?
The site is an information resource for the customer exploring the tools that KVR sells and the scientific issues surrounding protein-protein interactions. They should be able to navigate easily to their content of choice, while the whole site should convey a professionalism that enhanced KVR’s credibility.

WHAT DOES THE KVR BRAND STAND FOR?
KVR stands for illumination. Proteins are challenging to study, and KVR exists to help shed light on their workings.

WHAT ARE THE KEY VALUES OF THE KVR BRAND?
Integrity. Innovation. Insight.

WHAT ARE THE EXECUTIONAL MANDITORIES?
The look and feel is completely up for grabs. Nothing is off the table.

WHAT ARE THE DELIVERABLES?
We need new designs for the following templates:
http://cms.marlowbench.com/
http://cms.marlowbench.com/products-and-services/instruments-3/bench-top-instruments/
http://cms.marlowbench.com/category/lab-study/

```html
<!DOCTYPE html>
<html lang="en">
<head>
<meta charset="utf-8">
<title>KVR Inc</title>
<link rel="stylesheet" href="https://fonts.googleapis.com/css2?family=Ubuntu:wght@400;500;700&family=Open+Sans:wght@400;600&display=swap">
<style>
:root{
  --orange:#f7a823;
  --teal:#2c8fab;
  --ink:#4a4a4a;
  --white:#ffffff;
  --band:rgba(60,58,56,.62);
  --band-mid:#3a3736;
  --footer:#050505;
  --search:#8a8a8a;
}
*{margin:0;padding:0;box-sizing:border-box}
html,body{width:1200px;height:733px;overflow:hidden;background:var(--white)}
body{position:relative;font-family:"Open Sans",Arial,sans-serif}
.site-header{position:absolute;left:0;top:0;width:1200px;height:51px;background:var(--white);border-top:3px solid var(--orange);z-index:3}
.brand{position:absolute;left:184px;top:11px;font-family:"Ubuntu",Arial,sans-serif;font-weight:400;font-size:27px;letter-spacing:6px;color:#555;line-height:1}
.main-nav{position:absolute;top:15px;left:0;font-family:"Ubuntu",Arial,sans-serif;font-weight:500;font-size:14px;color:var(--ink)}
.main-nav a{position:absolute;white-space:nowrap;color:inherit;text-decoration:none}
.main-nav a.active{color:var(--orange)}
.nav-pointer{position:absolute;left:480px;top:48px;width:0;height:0;border-left:6px solid transparent;border-right:6px solid transparent;border-top:7px solid var(--white);z-index:4}
.search{position:absolute;left:896px;top:13px;width:119px;height:21px;background:var(--search);color:#d8d8d8;font-size:11px;padding:3px 7px;line-height:15px}
.search svg{position:absolute;right:5px;top:4px}
.hero{position:absolute;left:0;top:51px;width:1200px;height:628px;background:
  radial-gradient(ellipse 30% 35% at 55% 35%,#f1dcd0 0%,rgba(241,220,208,0) 100%),
  linear-gradient(90deg,#b9bcc0 0%,#d9dedf 18%,#c9d8b4 25%,#eee9e6 45%,#f4f0ee 60%,#8a8c90 80%,#2e3136 100%)}
.slide-caption{position:absolute;top:327px;left:0;width:1200px;text-align:center;font-size:12px;color:#111}
.slide-caption span{margin-left:8px;letter-spacing:-2px}
.dots{position:absolute;top:359px;left:575px;display:flex;gap:6px}
.dots i{width:8px;height:8px;border-radius:50%;background:var(--white);border:2px solid #222}
.dots i.on{background:var(--orange)}
.feature{position:absolute;top:490px;height:189px;background:var(--band);color:var(--white);text-align:center}
.feature.mid{background:var(--band-mid)}
.feature .disc{position:absolute;left:50%;top:-83px;width:105px;height:105px;margin-left:-52px;border-radius:50%;background:var(--white);display:flex;align-items:center;justify-content:center}
.feature.mid .disc{border:4px solid #2d2a29}
.feature h2{position:absolute;top:30px;left:0;width:100%;font-family:"Ubuntu",Arial,sans-serif;font-weight:500;font-size:24px}
.feature p{position:absolute;top:66px;left:50%;width:250px;margin-left:-125px;font-size:11.5px;line-height:16.2px;color:#eee}
.btn{position:absolute;top:141px;left:50%;width:148px;height:24px;margin-left:-74px;background:var(--teal);color:var(--white);font-family:"Ubuntu",Arial,sans-serif;font-size:14px;line-height:24px;text-decoration:none;display:flex;justify-content:center;align-items:center;gap:14px}
.btn.order{background:var(--orange)}
.site-footer{position:absolute;left:0;top:679px;width:1200px;height:54px;background:var(--footer);color:var(--white)}
.footer-nav{position:absolute;left:184px;top:21px;font-size:11px}
.footer-nav a{color:inherit;text-decoration:none}
.footer-nav b{font-weight:400;margin:0 6px}
.social{position:absolute;left:794px;top:18px;display:flex;gap:5px}
.social i{width:21px;height:21px;border-radius:50%;background:var(--white)}
.copyright{position:absolute;left:884px;top:20px;font-size:11.5px;color:#ccc}
.copyright em{font-style:normal;color:var(--orange)}
</style>
</head>
<body>
<header class="site-header">
  <div class="brand">KVR INC</div>
  <nav class="main-nav">
    <a style="left:345px">Company</a>
    <a class="active" style="left:425px">Products &amp; Services</a>
    <a style="left:567px">Learning Center</a>
    <a style="left:686px">Events</a>
    <a style="left:748px">KVR News</a>
    <a style="left:826px">Contact</a>
  </nav>
  <div class="search">Search
    <svg width="11" height="11" viewBox="0 0 11 11"><circle cx="4.5" cy="4.5" r="3.5" fill="none" stroke="#ccc" stroke-width="1.4"/><line x1="7" y1="7" x2="10" y2="10" stroke="#ccc" stroke-width="1.6"/></svg>
  </div>
</header>
<div class="nav-pointer"></div>

<section class="hero" role="img" aria-label="Photo of a researcher in a lab looking into a microscope">
  <p class="slide-caption">Lorem ipsum dolor sit amet, consectetur adipiscing elit...<span>›››</span></p>
  <div class="dots"><i class="on"></i><i></i><i></i><i></i></div>
</section>

<section class="feature" style="left:0;width:454px">
  <div class="disc"><svg width="26" height="34" viewBox="0 0 26 34"><path d="M9 8h8M10 8v8L3 30h20L16 16V8" fill="none" stroke="#666" stroke-width="2"/><path d="M6 24h14l3 6H3z" fill="#666"/><circle cx="13" cy="3" r="1.5" fill="#666"/></svg></div>
  <h2>Innovation</h2>
  <p>Lorem ipsum dolor sit amet, consectetur adipiscing elit. Proin placerat nulla massa, condimentum leo tincidunt vel. Consectetur adipiscing elit.</p>
  <a class="btn">Learn More <svg width="16" height="11" viewBox="0 0 16 11"><path d="M0 3.5h9V0l7 5.5-7 5.5V7.5H0z" fill="#fff"/></svg></a>
</section>
<section class="feature mid" style="left:454px;width:293px">
  <div class="disc"><svg width="34" height="36" viewBox="0 0 34 36"><path d="M12 4l6 3-4 8-6-3z" fill="#666"/><circle cx="14" cy="20" r="6" fill="none" stroke="#666" stroke-width="3"/><path d="M8 30c6 2 14 1 18-4M6 33h24" fill="none" stroke="#666" stroke-width="3"/></svg></div>
  <h2>Automation</h2>
  <p>Lorem ipsum dolor sit amet, consectetur adipiscing elit. Proin placerat nulla massa, condimentum leo tincidunt vel. Consectetur adipiscing elit.</p>
  <a class="btn order">Order Today <svg width="16" height="11" viewBox="0 0 16 11"><path d="M0 3.5h9V0l7 5.5-7 5.5V7.5H0z" fill="#fff"/></svg></a>
</section>
<section class="feature" style="left:747px;width:453px">
  <div class="disc"><svg width="38" height="32" viewBox="0 0 38 32"><circle cx="18" cy="12" r="8" fill="none" stroke="#666" stroke-width="3"/><line x1="12" y1="18" x2="3" y2="28" stroke="#666" stroke-width="4"/><circle cx="30" cy="10" r="2" fill="#666"/><circle cx="33" cy="20" r="2" fill="#666"/><circle cx="27" cy="24" r="2" fill="#666"/></svg></div>
  <h2>Research</h2>
  <p>Lorem ipsum dolor sit amet, consectetur adipiscing elit. Proin placerat nulla massa, condimentum leo tincidunt vel. Consectetur adipiscing elit.</p>
  <a class="btn">The Challenge <svg width="16" height="11" viewBox="0 0 16 11"><path d="M0 3.5h9V0l7 5.5-7 5.5V7.5H0z" fill="#fff"/></svg></a>
</section>

<footer class="site-footer">
  <nav class="footer-nav"><a>Company</a><b>-</b><a>Products &amp; Services</a><b>-</b><a>Learning Center</a><b>-</b><a>Events</a><b>-</b><a>KVR News</a><b>-</b><a>Contact</a></nav>
  <div class="social" aria-label="Social links"><i></i><i></i><i></i></div>
  <p class="copyright">Copyright © <em>KVR Inc.</em> 2013</p>
</footer>
</body>
</html>
```